Maple Grove Schools | brand new stationery!

We need stationery design with our new logo! Our company updated it's name and image and we like to incorporate the new one on our stationery, business cards and email signature. We are looking for fresh, new ideas!
Industry: Childcare, Elementary and Middle School
Company Name: Maple Grove Schools
Tagline: Bright Futures Start Here
Main colors: Blue, white and a little yellow
Star shape is something new for us! Do you see a way to incorporate it as a design element?

```html
<!DOCTYPE html>
<html lang="en">
<head>
<meta charset="utf-8">
<title>Maple Grove Schools – Business Card</title>
<link href="https://fonts.googleapis.com/css2?family=Montserrat:wght@500;600;700&family=Roboto:wght@400&display=swap" rel="stylesheet">
<style>
  :root {
    --brand-blue: #2b2a85;
    --brand-blue-soft: #3a3a98;
    --brand-yellow: #f5c211;
    --ink: #1e1e24;
    --text-grey: #6b6b70;
    --paper: #ffffff;
    --backdrop: #e6e6ea;
  }
  * { box-sizing: border-box; margin: 0; padding: 0; }
  html, body { width: 1200px; height: 1129px; overflow: hidden; }
  body {
    background: var(--backdrop);
    position: relative;
    font-family: "Roboto", Arial, sans-serif;
  }
  .card {
    position: absolute;
    left: 180px;
    width: 840px;
    height: 480px;
    box-shadow: 0 10px 30px rgba(0,0,0,0.18);
    overflow: hidden;
  }
  .card-back { top: 60px; }
  .star-pattern {
    width: 100%;
    height: 100%;
    background: radial-gradient(ellipse at 30% 40%, var(--brand-blue-soft), var(--brand-blue) 70%);
  }
  .card-front { top: 590px; background: var(--paper); }

  .brand {
    position: absolute;
    left: 40px;
    top: 90px;
    width: 320px;
    text-align: center;
  }
  .brand-dot {
    width: 90px;
    height: 90px;
    border-radius: 50%;
    background: var(--brand-blue);
    margin: 0 auto 22px;
  }
  .brand-name {
    font-family: "Montserrat", Arial, sans-serif;
    font-weight: 700;
    font-size: 34px;
    line-height: 1.1;
    color: var(--ink);
  }

  .divider {
    position: absolute;
    left: 400px;
    top: 80px;
    width: 2px;
    height: 240px;
    background: var(--brand-yellow);
  }

  .contact {
    position: absolute;
    left: 432px;
    top: 84px;
    right: 30px;
  }
  .person-name {
    font-family: "Montserrat", Arial, sans-serif;
    font-weight: 700;
    font-size: 25px;
    letter-spacing: 0.5px;
    color: var(--ink);
    text-transform: uppercase;
  }
  .person-title {
    font-family: "Montserrat", Arial, sans-serif;
    font-weight: 500;
    font-size: 20px;
    color: var(--brand-yellow);
    margin-top: 2px;
  }
  .address {
    font-size: 19px;
    line-height: 1.3;
    color: var(--text-grey);
    margin-top: 20px;
    font-style: normal;
  }
  .contact-list { list-style: none; margin-top: 8px; }
  .contact-item {
    display: flex;
    align-items: center;
    gap: 10px;
    font-size: 19px;
    line-height: 1.45;
    color: var(--text-grey);
  }
  .contact-icon { width: 20px; height: 20px; flex: none; }

  .tagline-band {
    position: absolute;
    left: 0;
    right: 0;
    top: 354px;
    height: 50px;
    background: var(--brand-blue);
    color: var(--paper);
    font-family: "Montserrat", Arial, sans-serif;
    font-weight: 500;
    font-size: 17px;
    letter-spacing: 2px;
    display: flex;
    align-items: center;
    justify-content: center;
  }
  .base-band {
    position: absolute;
    left: 0;
    right: 0;
    top: 412px;
    height: 36px;
    background: var(--brand-blue);
  }
</style>
</head>
<body>
  <section class="card card-back">
    <div class="star-pattern" role="img" aria-label="Repeating pattern of star emblems on deep blue"></div>
  </section>

  <section class="card card-front">
    <div class="brand">
      <div class="brand-dot"></div>
      <div class="brand-name">Maple Grove Schools</div>
    </div>

    <div class="divider"></div>

    <div class="contact">
      <div class="person-name">Daniel R. Whitford</div>
      <div class="person-title">Founder &amp; CEO</div>
      <address class="address">48 Elm Avenue, Suite 2<br>Lakeview, MA 01234</address>
      <ul class="contact-list">
        <li class="contact-item">
          <svg class="contact-icon" viewBox="0 0 24 24"><path fill="#2b2a85" d="M6.6 10.8a15.1 15.1 0 0 0 6.6 6.6l2.2-2.2c.3-.3.7-.4 1-.2 1.1.4 2.3.6 3.6.6.6 0 1 .4 1 1V20c0 .6-.4 1-1 1A17 17 0 0 1 3 4c0-.6.4-1 1-1h3.5c.6 0 1 .4 1 1 0 1.3.2 2.5.6 3.6.1.3 0 .7-.2 1z"/></svg>
          (555) 014-2290
        </li>
        <li class="contact-item">
          <svg class="contact-icon" viewBox="0 0 24 24"><rect x="2.5" y="5" width="19" height="14" fill="none" stroke="#2b2a85" stroke-width="2"/><path d="M2.5 5l9.5 8 9.5-8" fill="none" stroke="#2b2a85" stroke-width="2"/></svg>
          hello@maplegroveschools.com
        </li>
        <li class="contact-item">
          <svg class="contact-icon" viewBox="0 0 24 24" fill="none" stroke="#2b2a85" stroke-width="1.6"><circle cx="12" cy="12" r="9.5"/><ellipse cx="12" cy="12" rx="4.5" ry="9.5"/><path d="M2.5 12h19M4 7h16M4 17h16"/></svg>
          www.maplegroveschools.com
        </li>
      </ul>
    </div>

    <div class="tagline-band">Bright Futures Start Here</div>
    <div class="base-band"></div>
  </section>
</body>
</html>
```